Construction company that specializes in roofing and siding

https://maplecrestbuild.example/featured-projects/

https://www.bramwickhomesllc.example/#

https://www.tallgrovecontractors.example/residential-siding-services/

Please model a website after these examples
I posted a doc that has some content to get you started. I will upload more content and photos as the site progresses.

Coded - Design and coding required

5+ page

```html
<!DOCTYPE html>
<html lang="en">
<head>
<meta charset="utf-8">
<title>Stonegate Construction – Roofing and Siding in Minnesota</title>
<link href="https://fonts.googleapis.com/css2?family=Audiowide&family=Poppins:wght@400;500;600&display=swap" rel="stylesheet">
<style>
:root{
  --ink:#2b2b2b;
  --dark:#333333;
  --mid:#6b6b6b;
  --muted:#777777;
  --line:#9a9a9a;
  --paper:#ffffff;
  --soft:#f3f3f3;
  --card-border:#e2e2e2;
  --sky:#c9dcea;
  --roof:#6f757c;
}
*{box-sizing:border-box;margin:0;padding:0}
html,body{width:1200px;height:4594px;overflow:hidden}
body{font-family:"Poppins",sans-serif;color:var(--ink);background:var(--paper);position:relative}
.display{font-family:"Audiowide",sans-serif;letter-spacing:1px;text-transform:uppercase}
a{color:inherit;text-decoration:none}
.slant-btn{display:inline-block;background:var(--mid);color:#fff;font-size:16px;padding:10px 62px;clip-path:polygon(7% 0,100% 0,93% 100%,0 100%)}
.read{font-size:15px;color:var(--ink);display:inline-flex;align-items:center;gap:5px}
.read svg{width:14px;height:14px}

/* top bar */
.topbar{position:absolute;left:0;top:0;width:1200px;height:50px;background:var(--dark);color:#fff;font-size:13px;display:flex;align-items:center;padding-left:112px}
.topbar span{padding:0 14px;border-right:1px solid #666;display:flex;align-items:center;gap:6px}
.topbar span:first-child{padding-left:0}
.topbar span:nth-child(3){border:none}
.quote{position:absolute;right:0;top:0;height:50px;width:300px;background:#5b5b5b;clip-path:polygon(8% 0,100% 0,100% 100%,0 100%);display:flex;align-items:center;justify-content:center;gap:6px;font-size:13px}

/* nav */
.nav{position:absolute;top:50px;left:0;width:1200px;height:87px;background:#fff;display:flex;align-items:center}
.brand-box{width:330px;height:87px;background:var(--mid);clip-path:polygon(0 0,100% 0,93% 100%,0 100%);display:flex;align-items:center;padding-left:112px;gap:10px;color:#fff}
.brand-box .dot{width:44px;height:44px;border-radius:50%;background:#fff}
.brand-name{font-family:"Poppins",sans-serif;font-weight:600;font-size:17px;line-height:1.1}
.menu{display:flex;gap:30px;margin-left:50px;font-size:16px;color:#444}
.menu .on{font-weight:600;color:var(--ink)}

/* hero */
.hero{position:absolute;top:137px;left:0;width:1200px;height:631px;background:linear-gradient(180deg,#d7e5f0 0%,var(--sky) 45%,#8c939a 70%,var(--roof) 100%);text-align:center}
.hero h1{font-size:30px;line-height:36px;margin:66px auto 0;width:800px;color:var(--ink)}
.hero .slant-btn{margin-top:40px}

/* section heading with rules */
.sec-title{display:flex;align-items:center;justify-content:center;gap:30px;font-size:30px}
.sec-title::before,.sec-title::after{content:"";width:250px;height:2px;background:var(--dark)}

/* roofing */
.roofing{position:absolute;top:840px;left:0;width:1200px}
.roof-cards{display:flex;gap:40px;margin:50px 0 0 112px}
.roof-card{width:300px;height:358px;border:1px solid var(--card-border);border-top:5px solid #555;background:#fff;text-align:center;position:relative}
.roof-card.lift{box-shadow:0 8px 18px rgba(0,0,0,.18)}
.roof-card .ico{width:100px;height:100px;border-radius:50%;background:var(--mid);margin:30px auto 22px;display:flex;align-items:center;justify-content:center}
.roof-card .ico.light{background:#e7e7e7}
.roof-card h3{font-size:18px;font-weight:500}
.roof-card p{font-size:13px;color:var(--muted);line-height:20px;margin:12px 24px 0}
.roof-card .foot{position:absolute;bottom:0;left:0;right:0;height:62px;border-top:1px solid var(--card-border);display:flex;align-items:center;justify-content:center}

/* about */
.about{position:absolute;top:1374px;left:0;width:1200px;height:558px;background:var(--soft)}
.about .photo{position:absolute;left:112px;top:86px;width:420px;height:385px;background:linear-gradient(160deg,#b9c2c9 0%,#8a5d49 45%,#3f4a55 100%)}
.about .text{position:absolute;left:597px;top:80px;width:488px}
.about h2{font-size:30px;display:flex;align-items:center;gap:26px}
.about h2::after{content:"";flex:1;height:2px;background:var(--dark)}
.about p{font-size:15px;line-height:26px;color:#444;text-align:justify;margin-top:18px}
.about p+p{margin-top:8px}
.about .slant-btn{margin-top:20px}

/* siding */
.siding{position:absolute;top:2005px;left:0;width:1200px}
.side-cards{display:flex;gap:40px;margin:52px 0 0 112px}
.side-card{width:300px;height:256px;background:linear-gradient(180deg,#7a8087,#5d636a);color:#fff;text-align:center}
.side-card .ico{width:100px;height:100px;border-radius:50%;background:#fff;margin:26px auto 18px;display:flex;align-items:center;justify-content:center}
.side-card h3{font-size:18px;font-weight:500}
.side-card p{font-size:13px;line-height:20px;margin:4px 26px 0;color:#eee}
.arrows{display:flex;justify-content:center;gap:32px;margin-top:36px}
.arrows span{width:46px;height:46px;border-radius:50%;background:#111;display:flex;align-items:center;justify-content:center}

/* repair */
.repair{position:absolute;top:2480px;left:0;width:1200px;height:720px}
.repair h2{font-size:30px;display:flex;align-items:center;gap:26px;margin-left:112px;width:425px}
.repair h2::after{content:"";flex:1;height:2px;background:var(--dark)}
.repair .worker{position:absolute;right:0;top:320px;width:560px;height:400px;background:linear-gradient(200deg,#dfe3e6 0%,#b39a7a 55%,#8c7a64 100%);clip-path:polygon(62% 0,100% 0,100% 100%,0 100%,0 82%,30% 20%)}
.repair .ground{position:absolute;left:0;bottom:0;width:1200px;height:80px;background:linear-gradient(180deg,rgba(200,190,175,0),#b9ab97)}
.rep-item{position:absolute;display:flex;gap:30px;width:450px;z-index:1}
.rep-item .ico{flex:0 0 74px;height:74px;border-radius:50%;background:#e5e5e5;display:flex;align-items:center;justify-content:center}
.rep-item h3{font-size:18px;font-weight:500;margin-top:2px}
.rep-item p{font-size:13px;line-height:20px;color:var(--muted);margin:6px 0 6px;text-align:justify}

/* storm */
.storm{position:absolute;top:3270px;left:0;width:1200px}
.storm .sec-title::before,.storm .sec-title::after{width:190px}
.storm-cards{display:flex;gap:38px;margin:45px 0 0 112px}
.storm-card{width:300px}
.storm-card .pic{height:233px}
.storm-card h3{font-size:18px;font-weight:500;margin-top:22px}
.storm-card p{font-size:13px;line-height:20px;color:var(--muted);margin:10px 0 8px;text-align:justify}
.storm .center{text-align:center;margin-top:44px}

/* promise */
.promise{position:absolute;top:3905px;left:0;width:1200px;height:395px;background:linear-gradient(120deg,#2d2d2d 0%,#4a4743 50%,#6b5f52 100%);color:#fff}
.promise h2{font-size:30px;margin:66px 0 0 112px;display:flex;align-items:center;gap:20px;width:775px}
.promise h2::after{content:"";flex:1;height:2px;background:#fff}
.promise p{font-size:15px;line-height:26px;width:540px;margin:18px 0 0 112px}
.promise .sign{margin:24px 0 0 112px;font-size:20px;line-height:34px}
.promise .sign small{display:block;font-size:15px;line-height:16px}

/* footer */
.footer{position:absolute;top:4300px;left:0;width:1200px;height:294px;background:var(--dark);color:#fff;text-align:center}
.f-brand{display:flex;align-items:center;justify-content:center;gap:14px;margin-top:52px}
.f-brand .dot{width:70px;height:70px;border-radius:50%;background:#fff}
.f-brand span{font-size:28px;font-weight:600}
.f-menu{display:flex;justify-content:center;gap:34px;font-size:19px;margin-top:38px}
.f-rule{width:976px;height:1px;background:#aaa;margin:24px auto 0}
.f-copy{font-size:18px;margin-top:20px}
</style>
</head>
<body>

<div class="topbar">
  <span><svg width="13" height="12" viewBox="0 0 13 12"><path d="M1 2l3-1 5 2 3-1v9l-3 1-5-2-3 1z" fill="#fff"/></svg>Lorem ipsum dolor sit amet</span>
  <span><svg width="12" height="12" viewBox="0 0 12 12"><path d="M2 1l2 0 1 3-1.5 1a7 7 0 003.5 3.5L8 7l3 1v2a1 1 0 01-1 1A9 9 0 011 2a1 1 0 011-1z" fill="#fff"/></svg>Phone: +1 555 0100 2200</span>
  <span><svg width="13" height="10" viewBox="0 0 13 10"><rect width="13" height="10" rx="1" fill="#fff"/><path d="M0 1l6.5 5L13 1" stroke="#333" fill="none"/></svg>Mail: info@stonegatebuild.example</span>
  <a class="quote" href="#"><svg width="12" height="12" viewBox="0 0 12 12"><path d="M12 0L0 5l4 2 1 5 2-3 3 2z" fill="#fff"/></svg>Get a Free Quote</a>
</div>

<header class="nav">
  <div class="brand-box"><span class="dot"></span><span class="brand-name">Stonegate<br>Construction</span></div>
  <nav class="menu">
    <a class="on" href="#">Home</a><a href="#">Roofing ▾</a><a href="#">Siding ▾</a><a href="#">Gutters</a><a href="#">Windows Repair ▾</a><a href="#">Storm damage repair ▾</a>
  </nav>
</header>

<section class="hero" role="img" aria-label="Roofing crew installing shingles on a house roof under a blue sky">
  <h1 class="display">Stonegate Construction is your source for roofing and siding in Minnesota.</h1>
  <a class="slant-btn" href="#">Learn More</a>
</section>

<section class="roofing">
  <h2 class="sec-title display">Roofing</h2>
  <div class="roof-cards">
    <article class="roof-card lift">
      <div class="ico"><svg width="56" height="56" viewBox="0 0 56 56"><path d="M28 4L8 18v24l20 10 20-10V18z" fill="#fff"/><path d="M28 14v36M16 22v24M40 22v24" stroke="#6b6b6b" stroke-width="3"/></svg></div>
      <h3>Architectural Shingles</h3>
      <p>Architectural shingles are the most cost effective choice in roofing, that is why they are also the most common choice.</p>
      <div class="foot"><a class="read" href="#">Read More <svg viewBox="0 0 14 14"><circle cx="7" cy="7" r="7" fill="#2b2b2b"/><path d="M4 7h6M7 4l3 3-3 3" stroke="#fff" stroke-width="1.6" fill="none"/></svg></a></div>
    </article>
    <article class="roof-card">
      <div class="ico light"><svg width="64" height="40" viewBox="0 0 64 40"><path d="M4 28L36 6l24 14-32 16z" fill="#222"/><path d="M10 28l26-16 16 10" stroke="#fff" stroke-width="2" fill="none"/></svg></div>
      <h3>Standing Seam Steel Roofing</h3>
      <p>Standing seam steel roofing is durable and long lasting. For homes and businesses, it is considered a premium upgrade over architectural</p>
      <div class="foot"><a class="read" href="#">Read More <svg viewBox="0 0 14 14"><circle cx="7" cy="7" r="7" fill="#2b2b2b"/><path d="M4 7h6M7 4l3 3-3 3" stroke="#fff" stroke-width="1.6" fill="none"/></svg></a></div>
    </article>
    <article class="roof-card">
      <div class="ico light"><svg width="64" height="40" viewBox="0 0 64 40"><path d="M4 30L32 8l28 22z" fill="#222"/><rect x="4" y="32" width="56" height="4" fill="#222"/></svg></div>
      <h3>Agricultural Steel Roofing</h3>
      <p>In MN there are a lot of shops, barns, and garages that require a cost effective and long lasting roofing system. Look no further</p>
      <div class="foot"><a class="read" href="#">Read More <svg viewBox="0 0 14 14"><circle cx="7" cy="7" r="7" fill="#2b2b2b"/><path d="M4 7h6M7 4l3 3-3 3" stroke="#fff" stroke-width="1.6" fill="none"/></svg></a></div>
    </article>
  </div>
</section>

<section class="about">
  <div class="photo" role="img" aria-label="Roofer installing steel roofing panels beside a brick chimney"></div>
  <div class="text">
    <h2 class="display">About Us</h2>
    <p>In 2016 Eli Harper started helping people with their home improvement projects. His very first job was installing window trim for a wonderful homeowner in Forest lake MN. He did his best work and made sure he treated his first customer like family. Afterall, his first customer was Ruth Harper, his Mom.</p>
    <p>Today, Eli and the Stonegate Construction team are helping homeowners around Minnesota; carrying the spirit of his first job onto every job they touch.</p>
    <a class="slant-btn" href="#">Learn More</a>
  </div>
</section>

<section class="siding">
  <h2 class="sec-title display">Siding</h2>
  <div class="side-cards">
    <article class="side-card" role="img" aria-label="House exterior with vinyl siding">
      <div class="ico"><svg width="50" height="50" viewBox="0 0 50 50"><path d="M15 8v30M35 8v30M8 16l7-8 7 8M28 16l7-8 7 8" stroke="#111" stroke-width="4" fill="none"/><rect x="6" y="42" width="38" height="4" fill="#111"/></svg></div>
      <h3>Vinyl Siding</h3>
      <p>Vinyl siding is a great option to give your home's exterior a beautiful makeover.</p>
    </article>
    <article class="side-card" role="img" aria-label="House exterior with steel siding">
      <div class="ico"><svg width="46" height="50" viewBox="0 0 46 50"><path d="M4 4h38v42H4z" fill="#111"/><path d="M4 14h38M4 24h38M4 34h38" stroke="#fff" stroke-width="2"/></svg></div>
      <h3>Northline Steel Siding</h3>
      <p>Minnesota's own Northline steel siding offers a premium upgrade over vinyl siding.</p>
    </article>
    <article class="side-card" role="img" aria-label="House exterior with engineered wood siding">
      <div class="ico"><svg width="50" height="50" viewBox="0 0 50 50"><rect x="8" y="6" width="22" height="38" rx="4" fill="none" stroke="#111" stroke-width="4"/><path d="M8 16h14M8 26h14M8 36h14" stroke="#111" stroke-width="4"/><path d="M36 18l6 7-6 7" stroke="#111" stroke-width="3" fill="none"/></svg></div>
      <h3>TrueGrain Engineered Siding</h3>
      <p>TrueGrain engineered siding is a wood composite siding that mimics the look of real wood siding</p>
    </article>
  </div>
  <div class="arrows">
    <span><svg width="16" height="16" viewBox="0 0 16 16"><path d="M11 2L5 8l6 6" stroke="#fff" stroke-width="2.4" fill="none"/></svg></span>
    <span><svg width="16" height="16" viewBox="0 0 16 16"><path d="M5 2l6 6-6 6" stroke="#fff" stroke-width="2.4" fill="none"/></svg></span>
  </div>
</section>

<section class="repair">
  <h2 class="display">Repair</h2>
  <div class="worker" role="img" aria-label="Workers framing a roof with wooden trusses"></div>
  <div class="ground"></div>

  <div class="rep-item" style="left:112px;top:85px">
    <div class="ico"><svg width="36" height="30" viewBox="0 0 36 30"><path d="M2 14L18 2l16 12v14H2z" fill="#222"/><path d="M8 18h20M8 23h20" stroke="#e5e5e5" stroke-width="2"/></svg></div>
    <div><h3>Missing Shingles</h3><p>If you are missing shingles, Stonegate Construction can help you identify the matching</p><a class="read" href="#">Read More <svg viewBox="0 0 14 14"><circle cx="7" cy="7" r="7" fill="#2b2b2b"/><path d="M4 7h6M7 4l3 3-3 3" stroke="#fff" stroke-width="1.6" fill="none"/></svg></a></div>
  </div>
  <div class="rep-item" style="left:112px;top:225px">
    <div class="ico"><svg width="36" height="30" viewBox="0 0 36 30"><path d="M2 28L12 4h14l8 24z" fill="#222"/><path d="M10 12h16M7 20h22" stroke="#e5e5e5" stroke-width="2"/></svg></div>
    <div><h3>Leaking Roof</h3><p>If your roof is leaking, Stonegate Construction can help you identify the source</p><a class="read" href="#">Read More <svg viewBox="0 0 14 14"><circle cx="7" cy="7" r="7" fill="#2b2b2b"/><path d="M4 7h6M7 4l3 3-3 3" stroke="#fff" stroke-width="1.6" fill="none"/></svg></a></div>
  </div>
  <div class="rep-item" style="left:112px;top:365px">
    <div class="ico"><svg width="36" height="30" viewBox="0 0 36 30"><path d="M2 26L16 6l18 20z" fill="#222"/><path d="M14 8l10 0 10 18" stroke="#222" stroke-width="3" fill="none"/></svg></div>
    <div><h3>Leaking Roof</h3><p>If your roof is leaking, Stonegate Construction can help you identify the source</p><a class="read" href="#">Read More <svg viewBox="0 0 14 14"><circle cx="7" cy="7" r="7" fill="#2b2b2b"/><path d="M4 7h6M7 4l3 3-3 3" stroke="#fff" stroke-width="1.6" fill="none"/></svg></a></div>
  </div>
  <div class="rep-item" style="left:643px;top:85px">
    <div class="ico"><svg width="32" height="32" viewBox="0 0 32 32"><g fill="#222"><rect x="2" y="4" width="8" height="11" rx="2"/><rect x="12" y="4" width="8" height="11" rx="2"/><rect x="22" y="4" width="8" height="11" rx="2"/><rect x="2" y="17" width="8" height="11" rx="2"/><rect x="12" y="17" width="8" height="11" rx="2"/><rect x="22" y="17" width="8" height="11" rx="2"/></g></svg></div>
    <div><h3>Add Vents</h3><p>If you need to add vents to your house or garage, Stonegate Construction can help.</p><a class="read" href="#">Read More <svg viewBox="0 0 14 14"><circle cx="7" cy="7" r="7" fill="#2b2b2b"/><path d="M4 7h6M7 4l3 3-3 3" stroke="#fff" stroke-width="1.6" fill="none"/></svg></a></div>
  </div>
  <div class="rep-item" style="left:643px;top:222px">
    <div class="ico"><svg width="40" height="24" viewBox="0 0 40 24"><path d="M2 20L20 6l18 14" stroke="#222" stroke-width="4" fill="none"/></svg></div>
    <div><h3>Add Ridge Vent</h3><p>If you need to add a ridge vent to your house or garage, Stonegate Construction can help.</p><a class="read" href="#">Read More <svg viewBox="0 0 14 14"><circle cx="7" cy="7" r="7" fill="#2b2b2b"/><path d="M4 7h6M7 4l3 3-3 3" stroke="#fff" stroke-width="1.6" fill="none"/></svg></a></div>
  </div>
</section>

<section class="storm">
  <h2 class="sec-title display">Storm Damage Repair</h2>
  <div class="storm-cards">
    <article class="storm-card">
      <div class="pic" role="img" aria-label="Wind damaged shingles on a roof" style="background:linear-gradient(140deg,#8a8b8d 0%,#6a6c6f 50%,#4d4f52 100%)"></div>
      <h3>Wind Damage Repair</h3>
      <p>If you are missing roofing or siding after a storm, the first step is to have a licensed and insured professional evaluate</p>
      <a class="read" href="#">Read More <svg viewBox="0 0 14 14"><circle cx="7" cy="7" r="7" fill="#2b2b2b"/><path d="M4 7h6M7 4l3 3-3 3" stroke="#fff" stroke-width="1.6" fill="none"/></svg></a>
    </article>
    <article class="storm-card">
      <div class="pic" role="img" aria-label="Hail covered roof of a house with autumn trees" style="background:linear-gradient(160deg,#8fa6bd 0%,#3e4d60 55%,#c0783a 100%)"></div>
      <h3>Hail Damage Repair</h3>
      <p>If you are concerned about hail damage after a storm, the first step is to have a licensed and insured professional</p>
      <a class="read" href="#">Read More <svg viewBox="0 0 14 14"><circle cx="7" cy="7" r="7" fill="#2b2b2b"/><path d="M4 7h6M7 4l3 3-3 3" stroke="#fff" stroke-width="1.6" fill="none"/></svg></a>
    </article>
    <article class="storm-card">
      <div class="pic" role="img" aria-label="House with roof damaged by a fallen tree and blue tarp" style="background:linear-gradient(180deg,#6f8fb3 0%,#c9c4bb 50%,#7c7c7c 100%)"></div>
      <h3>Tree Damage Repair</h3>
      <p>If you are concerned about tree damage after a storm, the first step is to have a licensed and insured</p>
      <a class="read" href="#">Read More <svg viewBox="0 0 14 14"><circle cx="7" cy="7" r="7" fill="#2b2b2b"/><path d="M4 7h6M7 4l3 3-3 3" stroke="#fff" stroke-width="1.6" fill="none"/></svg></a>
    </article>
  </div>
  <div class="center"><a class="slant-btn" href="#">View More</a></div>
</section>

<section class="promise" role="img" aria-label="Close view of hands fitting roof tiles">
  <h2 class="display">The Stonegate Promise</h2>
  <p>You deserve timely service, high quality materials, expert installation, and an honest warranty. That is what we promise to deliver. I invite you to put us to the test today.</p>
  <div class="sign">Sincerely,<br>Eli Harper, Owner<small>Stonegate Construction</small></div>
</section>

<footer class="footer">
  <div class="f-brand"><span class="dot"></span><span>Stonegate Construction</span></div>
  <nav class="f-menu"><a href="#">Home</a><a href="#">Roofing</a><a href="#">Siding</a><a href="#">Gutters</a><a href="#">Windows Repair</a><a href="#">Storm damage repair</a></nav>
  <div class="f-rule"></div>
  <p class="f-copy">© Copyright Stonegate Construction 2024. All Right Reserved.</p>
</footer>

</body>
</html>
```